Lantern Co. Supplement General Packaging Design

I am looking for a design template to design all of my various supplements and other products around. Meaning that this design should be able to just be able to change around words, up to a few small images, and text to suit my other various products.

The brand name is Lantern Co. and the slogan is: Heros Are Made
This is For an Apple Cider Vinegar Gummy, and include these top three things: Vegan, Gluten Free, Non-GMO somewhere in the design.

I want the design to have a luxurious feel. With some kind of design element where the logo is sort of the secondary aspect of the design.

Target Market(s)

Men age 24-45

Industry/Entity Type

Supplement

Requirements
Must have
• MUST HAVE A "vintage" LOOK AND FEEL. MUST HAVE ANOTHER design element besides the logo. (Something Vintage) MUST USE THE PROVIDED TEMPLATE A PDF IN THE FILES BELOW LABELED " TEMPLATE" and the LOGO PROVIDED under "Lantern Co. 2" OR "lantern co.3" whichever is better suited for the design. Bold design. Another color besides black to stand out. Use the lantern co logo which is below in the provided images. The design should go around the logo and fit the same aesthetic. The rest are for inspiration, what I like.

```html
<!DOCTYPE html>
<html lang="en">
<head>
<meta charset="UTF-8">
<title>Lantern Co. — Supplement Label</title>
<link rel="stylesheet" href="https://fonts.googleapis.com/css2?family=Montserrat:wght@200;400;500&display=swap">
<style>
  :root {
    --ink: #141414;
    --gold-deep: #b8892c;
    --gold: #e6c064;
    --gold-light: #f6e08f;
    --text-gold: #e9c35f;
  }
  html, body {
    margin: 0;
    padding: 0;
    width: 1200px;
    height: 1200px;
    overflow: hidden;
    background: var(--ink);
  }
  .label {
    position: relative;
    width: 1200px;
    height: 1200px;
    background: var(--ink);
    font-family: "Montserrat", "Helvetica Neue", Arial, sans-serif;
  }
  .label__frame {
    position: absolute;
    inset: 0;
  }
  .brand-mark {
    position: absolute;
    left: 498px;
    top: 352px;
    width: 230px;
    height: 230px;
    box-sizing: border-box;
    border: 4px solid var(--gold);
  }
  .brand-name {
    position: absolute;
    left: 0;
    right: 0;
    top: 624px;
    margin: 0;
    text-align: center;
    font-weight: 200;
    font-size: 78px;
    letter-spacing: 1px;
    line-height: 1;
    color: var(--text-gold);
  }
  .slogan-row {
    position: absolute;
    left: 177px;
    right: 180px;
    top: 764px;
    display: flex;
    align-items: center;
    gap: 36px;
  }
  .slogan-row__rule {
    flex: 1;
    height: 2px;
    background: linear-gradient(90deg, var(--gold-deep), var(--gold-light), var(--gold-deep));
  }
  .slogan {
    margin: 0;
    font-weight: 400;
    font-size: 26px;
    letter-spacing: 1px;
    color: var(--text-gold);
    white-space: nowrap;
  }
  .claims {
    position: absolute;
    left: 0;
    right: 0;
    top: 857px;
    margin: 0;
    text-align: center;
    font-weight: 500;
    font-size: 17.5px;
    letter-spacing: 0.6px;
    color: var(--text-gold);
  }
</style>
</head>
<body>
  <main class="label">
    <svg class="label__frame" width="1200" height="1200" viewBox="0 0 1200 1200" aria-hidden="true">
      <defs>
        <linearGradient id="goldStroke" x1="0" y1="0" x2="1" y2="1">
          <stop offset="0" stop-color="#f6e08f"/>
          <stop offset="0.35" stop-color="#c99a3a"/>
          <stop offset="0.65" stop-color="#f3d47c"/>
          <stop offset="1" stop-color="#b8892c"/>
        </linearGradient>
      </defs>
      <path class="frame-outer" fill="none" stroke="url(#goldStroke)" stroke-width="4"
        d="M 214 114 H 986 A 100 100 0 0 0 1086 214 V 986 A 100 100 0 0 0 986 1086 H 214 A 100 100 0 0 0 114 986 V 214 A 100 100 0 0 0 214 114 Z"/>
      <path class="frame-inner" fill="none" stroke="url(#goldStroke)" stroke-width="4"
        d="M 226 126 H 974 A 112 112 0 0 0 1074 226 V 974 A 112 112 0 0 0 974 1074 H 226 A 112 112 0 0 0 126 974 V 226 A 112 112 0 0 0 226 126 Z"/>
    </svg>

    <div class="brand-mark" role="img" aria-label="Lantern Co. brand mark"></div>

    <h1 class="brand-name">LANTERN CO.</h1>

    <div class="slogan-row">
      <span class="slogan-row__rule"></span>
      <p class="slogan">HEROS ARE MADE</p>
      <span class="slogan-row__rule"></span>
    </div>

    <p class="claims">VEGAN, GLUTEN FREE &amp; NON-GMO SUPPLEMENT</p>
  </main>
</body>
</html>
```